Marlowe Crest Realty business card design

Looking for an upscale and clean business card design and updated logo. I sell to a very high-end south Florida real estate market.
Target Market(s)
High-end real estate in south Florida real estate market
Industry/Entity Type
Real Estate Agent
Contact Information for Business Card
Marlowe Crest Realty, Inc
738 West Pinecrest Ave, Suite 410/510, Fort Lauderdale, FL 33308
Gary Whitlock - Broker/Owner
954-327-8846 Direct
garyshomes@quellmail.com
Website: DwellTarrowBay.com
Font styles to use
Other font styles liked:
- Copperplate Gothic, Georgia, etc.
Requirements
Must have
- My photo, company name, my name and title, all info stated in Details above
Nice to have
- Luxury home design element, waterfront

```html
<!DOCTYPE html>
<html lang="en">
<head>
<meta charset="utf-8">
<title>Marlowe Crest Realty – Business Card</title>
<link href="https://fonts.googleapis.com/css2?family=Arimo:wght@400;700&family=Crimson+Text:wght@400&display=swap" rel="stylesheet">
<style>
  :root {
    --stage: #2b2b2d;
    --ink: #050505;
    --paper: #ffffff;
    --gold: #f5c431;
    --gold-deep: #e9b21c;
    --text-dark: #111111;
    --photo-blue: #2d4a9a;
    --photo-pink: #f1c9d4;
  }
  html, body {
    margin: 0;
    width: 1200px;
    height: 900px;
    overflow: hidden;
    background: var(--stage);
  }
  .canvas {
    position: relative;
    width: 1200px;
    height: 900px;
  }
  .card {
    position: absolute;
    width: 630px;
    height: 360px;
    border-radius: 22px;
    overflow: hidden;
    box-shadow: 0 14px 30px rgba(0,0,0,.45);
  }
  .card-back {
    left: 90px;
    top: 70px;
    background: var(--ink);
  }
  .card-front {
    left: 480px;
    top: 470px;
    background: var(--paper);
  }
  .card svg.shape {
    position: absolute;
    inset: 0;
  }
  .brand {
    position: absolute;
    display: flex;
    align-items: center;
    font-family: "Crimson Text", Georgia, serif;
    font-weight: 400;
    color: var(--paper);
    line-height: 1.05;
    letter-spacing: .5px;
  }
  .brand-mark {
    flex: none;
    border-radius: 50%;
    background: var(--gold);
  }
  .card-back .brand {
    left: 110px;
    top: 140px;
    font-size: 34px;
    gap: 22px;
  }
  .card-back .brand-mark { width: 62px; height: 62px; }
  .card-front .brand {
    right: 34px;
    top: 24px;
    font-size: 19px;
    gap: 12px;
  }
  .card-front .brand-mark { width: 34px; height: 34px; }
  .portrait {
    position: absolute;
    left: 40px;
    top: 150px;
    width: 270px;
    height: 210px;
    background: linear-gradient(180deg, var(--photo-pink) 0%, #c9a6a8 35%, var(--photo-blue) 60%, #22397a 100%);
    clip-path: polygon(32% 0, 62% 0, 70% 38%, 100% 55%, 100% 100%, 0 100%, 0 65%, 26% 40%);
  }
  .agent {
    position: absolute;
    left: 330px;
    top: 198px;
    font-family: Arimo, Arial, sans-serif;
  }
  .agent-name {
    margin: 0;
    font-size: 27px;
    font-weight: 700;
    color: var(--gold);
    letter-spacing: .3px;
  }
  .agent-title {
    margin: 0 0 12px;
    font-size: 16px;
    color: var(--text-dark);
  }
  .contact-list {
    list-style: none;
    margin: 0;
    padding: 0;
    font-size: 16px;
    color: var(--text-dark);
  }
  .contact-list li {
    display: flex;
    align-items: center;
    gap: 12px;
    margin-bottom: 6px;
  }
  .contact-list svg { width: 16px; height: 16px; flex: none; }
</style>
</head>
<body>
<main class="canvas">

  <section class="card card-back" aria-label="Card back">
    <div class="brand">
      <span class="brand-mark"></span>
      <span>Marlowe Crest<br>&nbsp;&nbsp;Realty, Inc.</span>
    </div>
  </section>

  <section class="card card-front" aria-label="Card front">
    <svg class="shape" width="630" height="360" viewBox="0 0 630 360">
      <path d="M0 0 H630 V108 C560 140 470 150 360 150 C230 150 110 150 0 172 Z" fill="var(--ink)"/>
      <path d="M630 112 C560 146 470 156 360 156 C230 156 110 158 0 182" fill="none" stroke="var(--gold)" stroke-width="5"/>
      <path d="M600 130 C530 158 450 164 340 165 C230 166 130 170 40 188" fill="none" stroke="var(--gold-deep)" stroke-width="2"/>
    </svg>

    <div class="brand">
      <span class="brand-mark"></span>
      <span>Marlowe Crest<br>&nbsp;&nbsp;Realty, Inc.</span>
    </div>

    <div class="portrait" role="img" aria-label="Portrait photo of the agent in a blue checked blazer and pink shirt"></div>

    <div class="agent">
      <h1 class="agent-name">Gary Whitlock</h1>
      <p class="agent-title">Manager</p>
      <ul class="contact-list">
        <li>
          <svg viewBox="0 0 16 16" aria-hidden="true"><path d="M3 1.5 L6 1.5 L7 5 L5.2 6.3 C6 8 7.8 9.9 9.7 10.8 L11 9 L14.5 10 L14.5 13 C14.5 14 13.6 14.6 12.6 14.5 C6.8 14 2 9.2 1.5 3.4 C1.4 2.4 2 1.5 3 1.5 Z" fill="var(--gold)"/></svg>
          <span>327-8846</span>
        </li>
        <li>
          <svg viewBox="0 0 16 16" aria-hidden="true"><rect x="1" y="3" width="14" height="10" rx="1" fill="var(--gold)"/><path d="M1.5 3.5 L8 9 L14.5 3.5" fill="none" stroke="var(--paper)" stroke-width="1.3"/></svg>
          <span>youremail@quellmail.com</span>
        </li>
        <li>
          <svg viewBox="0 0 16 16" aria-hidden="true"><circle cx="8" cy="8" r="7" fill="var(--gold)"/><circle cx="8" cy="8" r="3" fill="none" stroke="var(--paper)" stroke-width="1.4"/></svg>
          <span>www.yourwebsite.com</span>
        </li>
      </ul>
    </div>
  </section>

</main>
</body>
</html>
```